Pimping of pitching slides for a startup in the medical field

We have a powerpoint presentation for pitching events (for potential investors) and the slides need some improvement.
Please create:
1. A slide master - a layout template including the Meditrova logo, a title, and some empty space to be filled with pictures and/or text. This empty space needs to have a white background, as many of our illustrations have a white background and it is easier for printing later.
2. Pimp the existing slides (they are attached). You can improve all of them, but you don't have to. The following slides need to be reworked for sure however: 1, 13, 14, 15, 20, 21, 22, 23. Please use the text on the slides. However, you may change or add or remove the pictures and everything else.
If you want to use additional visual material, please feel free to do so.
You can use visual material from http://www.pixvaultimages.example/ and we will pay the royalties later. Just use the pictures with the watermarks in the meantime and let us know, which one it is. Also, try to use pictures that cost 15 credits or less.
You can also use any visual material you find on our websites and also any single illustration from our product video. Let us know if you need something.
Websites:
Company - http://www.meditrova-example.com/
Product - http://www.trackyourache.example/
Product video:
https://www.vidstreamhub.example/watch?v=Qa3pLm9xZtR
In general, the design should look modern, yet coming from a trustworthy company.
Learn more about us through the above mentioned links. The designs on the websites do however not need to be taken as a template - we want to change it eventually.
Looking forward seeing your suggestions!
Hi everyone,
http://shotgallery.example/shots/5820391-Summit-Slide-Layout/attachments/730184
http://designmarket.example/item/olu-deluxe-slide-layout/7261038?ref=tvbk5527
http://www.portfoliohive.example/gallery/Fresh-Slidedeck/36291748
http://shotgallery.example/shots/5894120-Slidedeck-layout/attachments/735512
http://www.portfoliohive.example/gallery/Venture-Deck-Slides/36804217
Medical

```html
<!DOCTYPE html>
<html lang="en">
<head>
<meta charset="utf-8">
<title>Learning from Others</title>
<link rel="stylesheet" href="https://fonts.googleapis.com/css2?family=Questrial&family=Arimo:wght@400;700&display=swap">
<style>
  :root {
    --deep-blue: #1d5aa8;
    --mid-blue: #4f86c6;
    --pale-blue: #c9d6e8;
    --band-blue: #a9bcd8;
    --canvas-top: #f4f6fa;
    --canvas-bottom: #e3e9f2;
    --ink: #111111;
    --white: #ffffff;
  }
  html, body {
    margin: 0;
    padding: 0;
    overflow: hidden;
    background: var(--white);
  }
  .slide {
    position: relative;
    width: 1200px;
    height: 895px;
    overflow: hidden;
    background: linear-gradient(180deg, var(--canvas-top) 0%, var(--white) 40%, var(--canvas-bottom) 100%);
    font-family: "Arimo", Arial, sans-serif;
  }
  .header-waves, .footer-waves {
    position: absolute;
    left: 0;
    width: 1200px;
  }
  .header-waves { top: 0; height: 200px; }
  .footer-waves { bottom: 0; height: 80px; }
  .title-band {
    position: absolute;
    left: 0;
    top: 42px;
    width: 1200px;
    height: 72px;
    background: linear-gradient(90deg, var(--band-blue) 0%, rgba(169,188,216,0.85) 55%, rgba(169,188,216,0) 100%);
  }
  .slide-title {
    position: absolute;
    left: 200px;
    top: 52px;
    margin: 0;
    font-family: "Questrial", "Century Gothic", sans-serif;
    font-weight: 400;
    font-size: 45px;
    letter-spacing: 1px;
    color: var(--white);
    line-height: 52px;
    -webkit-text-stroke: 0.8px var(--white);
  }
  .brand {
    position: absolute;
    right: 30px;
    top: 46px;
    display: flex;
    align-items: center;
    gap: 10px;
    font-family: "Questrial", "Century Gothic", sans-serif;
    font-size: 34px;
    color: var(--white);
  }
  .brand-dot {
    width: 26px;
    height: 26px;
    border-radius: 50%;
    background: var(--white);
  }
  .process-illustration {
    position: absolute;
    left: 30px;
    top: 352px;
    width: 805px;
    height: 448px;
    background: linear-gradient(135deg, #fbe3cf 0%, #f3f6fa 45%, #d6e6f6 100%);
    clip-path: polygon(0 0, 480px 0, 480px 102px, 805px 102px, 805px 448px, 0 448px);
  }
  .clustering {
    position: absolute;
    right: 43px;
    top: 253px;
    text-align: right;
    color: var(--ink);
  }
  .clustering-heading {
    margin: 0 0 34px;
    font-weight: 700;
    font-size: 27px;
    letter-spacing: 0.5px;
  }
  .criteria {
    list-style: none;
    margin: 0;
    padding: 0;
    font-size: 34px;
    letter-spacing: 0.4px;
    font-variant: small-caps;
    line-height: 43px;
  }
</style>
</head>
<body>
<main class="slide">
  <svg class="header-waves" viewBox="0 0 1200 200" preserveAspectRatio="none" aria-hidden="true">
    <defs>
      <linearGradient id="waveBlue" x1="0" y1="0" x2="1" y2="0">
        <stop offset="0" stop-color="#e8eef6"/>
        <stop offset="0.55" stop-color="#6f9bd0"/>
        <stop offset="1" stop-color="#1d5aa8"/>
      </linearGradient>
    </defs>
    <path d="M0 0 H1200 V200 C1120 120 1000 60 820 40 C560 14 260 30 0 44 Z" fill="url(#waveBlue)"/>
    <path d="M500 0 C800 20 1050 60 1200 150 V0 Z" fill="#1d5aa8" opacity="0.55"/>
  </svg>
  <svg class="footer-waves" viewBox="0 0 1200 80" preserveAspectRatio="none" aria-hidden="true">
    <path d="M0 30 C300 10 800 20 1200 0 V80 H0 Z" fill="#c3d1e6"/>
    <path d="M0 55 C400 35 800 45 1200 30 V80 H0 Z" fill="#8fa9d0" opacity="0.7"/>
  </svg>

  <div class="title-band"></div>
  <h1 class="slide-title">LEARNING FROM OTHERS</h1>

  <div class="brand"><span class="brand-dot"></span><span class="brand-name">Meditrova</span></div>

  <div class="process-illustration" role="img" aria-label="Sketch of a funnel feeding mixed shapes into a sigma calculator that sorts them into matching piles, with a cheering figure beside a flag"></div>

  <section class="clustering">
    <h2 class="clustering-heading">CLUSTERING BASED ON:</h2>
    <ul class="criteria">
      <li>Onset of pain</li>
      <li>Pain location</li>
      <li>Pain quality (hot, cold, electrifying, etc.)</li>
      <li>Time of occurrence</li>
      <li>Additional symptoms</li>
      <li>Effect of drugs</li>
      <li>Diagnoses</li>
      <li>etc.</li>
    </ul>
  </section>
</main>
</body>
</html>
```